MRT Property - Business Cards

Looking for a business card & general letterhead, signage etc design for our new logo.

Colours:
000a20
0056a2
00b5ef
0088ce
68cef2

Fonts:
Poppins
Karla

Please keep look and feel of new brand - example in the zip package I sent.

```html
<!DOCTYPE html>
<html lang="en">
<head>
<meta charset="utf-8">
<title>MRT Property – Business Card</title>
<link rel="stylesheet" href="https://fonts.googleapis.com/css2?family=Montserrat:wght@400;500;700&family=Yanone+Kaffeesatz:wght@300;400&display=swap">
<style>
  :root {
    --backdrop: #999999;
    --ink: #111527;
    --navy: #000a20;
    --brand-blue: #0056a2;
    --back-blue: #0b57a6;
    --sky: #00b5ef;
    --mid-blue: #0088ce;
    --pale-blue: #68cef2;
    --icon-blue: #1b8ad0;
    --text-light: #e8ecf3;
    --white: #ffffff;
  }
  * { margin: 0; padding: 0; box-sizing: border-box; }
  html, body {
    width: 1093px; height: 1200px; overflow: hidden;
    background: var(--backdrop);
    font-family: "Montserrat", Arial, sans-serif;
  }
  .card {
    position: absolute;
    left: 265px;
    width: 580px;
    border-radius: 21px;
    overflow: hidden;
  }
  .card-front { top: 225px; height: 362px; background: var(--ink); }
  .card-back { top: 616px; height: 365px; background: var(--back-blue); }

  .front-artwork {
    position: absolute; left: 0; top: 0;
    width: 288px; height: 362px;
    background: linear-gradient(150deg, var(--sky) 0%, var(--mid-blue) 45%, var(--pale-blue) 100%);
    border-radius: 0 0 190px 0;
    opacity: 0.9;
  }

  .front-details { position: absolute; inset: 0; color: var(--text-light); }
  .front-details > * { position: absolute; left: 304px; white-space: nowrap; }

  .company-name {
    font-weight: 700;
    font-size: 26px;
    line-height: 1;
    color: var(--brand-blue);
  }
  .front-details .company-name { left: 300px; top: 66px; }
  .person-name {
    top: 150px;
    font-family: "Yanone Kaffeesatz", "Arial Narrow", sans-serif;
    font-weight: 300;
    font-size: 31px;
    line-height: 1;
    color: var(--icon-blue);
  }
  .person-role { top: 180px; font-size: 13px; line-height: 16px; }
  .address {
    top: 216px;
    font-style: normal;
    font-size: 13.5px;
    line-height: 16px;
  }
  .contact-list { top: 270px; list-style: none; font-size: 13.5px; }
  .contact-list li {
    display: flex; align-items: center;
    height: 18px; margin-bottom: 7px;
  }
  .contact-list svg { width: 12px; height: 12px; margin-right: 9px; flex: none; }

  .back-pattern {
    position: absolute; inset: 0;
    background:
      radial-gradient(ellipse at 0% 0%, rgba(0,181,239,0.55) 0%, rgba(0,136,206,0.25) 35%, rgba(0,86,162,0) 65%),
      linear-gradient(150deg, rgba(27,111,184,0.2) 0%, rgba(30,63,124,0.45) 70%);
  }
  .back-logo {
    position: absolute; right: 111px; top: 278px;
    display: flex; align-items: center;
  }
  .back-logo .mark-dot {
    width: 16px; height: 16px; border-radius: 50%;
    background: var(--pale-blue);
    margin-right: 8px;
  }
  .back-logo .company-name { font-size: 21px; color: var(--white); }
</style>
</head>
<body>

<section class="card card-front">
  <div class="front-artwork" role="img" aria-label="Large brand sail artwork in sky, mid and pale blue"></div>

  <div class="front-details">
    <div class="company-name">MRT Property</div>
    <div class="person-name">Dana Whitfield</div>
    <div class="person-role">Managing Director</div>
    <address class="address">240 Cedar Ridge Road<br>Brandon, MS 39042</address>
    <ul class="contact-list">
      <li>
        <svg viewBox="0 0 24 24" aria-hidden="true"><path fill="var(--icon-blue)" d="M6.6 10.8a15.1 15.1 0 0 0 6.6 6.6l2.2-2.2a1 1 0 0 1 1-.25 11.4 11.4 0 0 0 3.6.57 1 1 0 0 1 1 1V20a1 1 0 0 1-1 1A17 17 0 0 1 3 4a1 1 0 0 1 1-1h3.5a1 1 0 0 1 1 1c0 1.25.2 2.450.57 3.57a1 1 0 0 1-.25 1z"/></svg>
        888.555.0142
      </li>
      <li>
        <svg viewBox="0 0 24 24" aria-hidden="true"><path fill="var(--icon-blue)" d="M2 5h20v14H2z"/><path fill="none" stroke="var(--ink)" stroke-width="1.8" d="M2 6l10 7 10-7"/></svg>
        info@mrtproperty.com
      </li>
      <li>
        <svg viewBox="0 0 24 24" aria-hidden="true"><circle cx="12" cy="12" r="10" fill="var(--icon-blue)"/><path fill="none" stroke="var(--ink)" stroke-width="1.4" d="M2 12h20M12 2c3 3 3 17 0 20M12 2c-3 3-3 17 0 20"/></svg>
        www.mrtproperty.com
      </li>
    </ul>
  </div>
</section>

<section class="card card-back">
  <div class="back-pattern" role="img" aria-label="Repeating brand sail pattern fading from light to dark blue"></div>
  <div class="back-logo">
    <span class="mark-dot"></span>
    <span class="company-name">MRT Property</span>
  </div>
</section>

</body>
</html>
```